Corporate Travel Technology Company needs new Business Card design

We need a new business card design to reflect our re-branded company. Our company is called tolvEn (pronounced tolvenn) and we provide Business Intelligence and Smart Corporate Journeys solutions for the corporate travel industry. Our multinational customers use our solutions to manage large travel budgets and frequent travellers, as well as to save money and reduce risk. We'd like to see designs that use the blue and green palette as well as our corporate logo (attached below). The design should communicate innovation, insight, forward thinking, contemporary, trusted.

Target Market(s)

Large multinational corporates and Travel Agencies.

Industry/Entity Type

Business

Contact Information for Business Card

Rosalind Mercer
Chief Executive
tolvEn
Phone number - +61 (0)2 8134 2907
Email address - rosalind.mercer@tolven-example.com
Mobile number - +61 (0)438 516 702
www.tolven-example.com

Font styles to use
Other font styles liked:
• Please use font as close to corporate logo as possible

Colors
0255a3
0393ce
00a990
33b8a4
33a6d7
3176b5

Requirements
Must have
• Please include the words;
• Smart Corporate Journeys
• Clearer Insight for Every Trip Budget
• Use corporate logo - although icon can be stylised if needed

```html
<!DOCTYPE html>
<html lang="en">
<head>
<meta charset="utf-8">
<title>tolvEn business card</title>
<link rel="stylesheet" href="https://fonts.googleapis.com/css2?family=Carlito:ital,wght@0,400;0,700;1,400&display=swap">
<style>
  :root {
    --bg: #8f9090;
    --sky: #00adef;
    --slate: #4a5c5b;
    --white: #ffffff;
    --ink: #4a5857;
  }
  * { margin: 0; padding: 0; box-sizing: border-box; }
  html, body { width: 1105px; height: 1200px; overflow: hidden; }
  body {
    background: var(--bg);
    font-family: "Carlito", "Calibri", sans-serif;
    position: relative;
  }
  .card {
    position: absolute;
    left: 182px;
    width: 747px;
    height: 425px;
    overflow: hidden;
  }
  .card-front { top: 119px; background: var(--sky); }
  .card-back { top: 637px; background: var(--white); }

  .side-band {
    position: absolute;
    left: 0; top: 0;
    width: 40px; height: 100%;
    background: var(--slate);
  }
  .holder {
    position: absolute;
    left: 80px; top: 165px;
    width: 270px;
    text-align: center;
    color: var(--white);
  }
  .holder-name { font-weight: 700; font-size: 33px; line-height: 1.1; white-space: nowrap; }
  .holder-role { font-size: 26px; line-height: 1.2; }

  .brand-front {
    position: absolute;
    right: 36px; top: 72px;
    display: flex; align-items: center; gap: 12px;
    color: var(--white);
    font-size: 44px; font-weight: 700;
  }
  .brand-dot {
    width: 22px; height: 22px; border-radius: 50%;
    background: var(--white);
  }

  .contact-list {
    position: absolute;
    right: 26px; top: 225px;
    list-style: none;
    color: var(--white);
    font-size: 18px;
  }
  .contact-list li {
    display: flex; align-items: center; justify-content: flex-end;
    gap: 10px; height: 28.5px; white-space: nowrap;
  }
  .contact-list svg { width: 18px; height: 18px; fill: var(--white); flex: none; }

  .taglines {
    position: absolute;
    right: 26px; top: 350px;
    list-style: none;
    color: var(--white);
    font-size: 18px; font-style: italic;
  }
  .taglines li {
    display: flex; align-items: center; justify-content: flex-end;
    gap: 14px; height: 25px; white-space: nowrap;
  }
  .taglines li::after {
    content: ""; width: 8px; height: 8px; border-radius: 50%;
    background: var(--white); margin-right: 5px; flex: none;
  }

  .brand-back {
    position: absolute;
    left: 0; right: 0; top: 110px;
    display: flex; flex-direction: column; align-items: center; gap: 14px;
  }
  .brand-back-dot {
    width: 70px; height: 70px; border-radius: 50%;
    background: var(--sky);
  }
  .brand-back-name {
    color: var(--ink);
    font-size: 86px; font-weight: 400; line-height: 1;
    letter-spacing: 1px;
  }
</style>
</head>
<body>
  <section class="card card-front">
    <div class="side-band"></div>
    <div class="holder">
      <p class="holder-name">Rosalind Mercer</p>
      <p class="holder-role">Chief Executive</p>
    </div>
    <div class="brand-front"><span class="brand-dot"></span>tolvEn</div>
    <ul class="contact-list">
      <li>+61 (0)2 8134 2907
        <svg viewBox="0 0 24 24"><path d="M6.6 10.8a15 15 0 0 0 6.6 6.6l2.2-2.2c.3-.3.7-.4 1-.2 1.1.4 2.3.6 3.6.6.6 0 1 .4 1 1V20c0 .6-.4 1-1 1A17 17 0 0 1 3 4c0-.6.4-1 1-1h3.5c.6 0 1 .4 1 1 0 1.3.2 2.5.6 3.6.1.3 0 .7-.2 1z"/></svg></li>
      <li>+61 (0)438 516 702
        <svg viewBox="0 0 24 24"><path d="M7 1h10a2 2 0 0 1 2 2v18a2 2 0 0 1-2 2H7a2 2 0 0 1-2-2V3a2 2 0 0 1 2-2zm0 3v14h10V4zm5 15.5a1.2 1.2 0 1 0 0 2.4 1.2 1.2 0 0 0 0-2.4z"/></svg></li>
      <li>www.tolven-example.com
        <svg viewBox="0 0 24 24"><path d="M12 2a10 10 0 1 0 0 20 10 10 0 0 0 0-20zm0 2c1 0 2.3 2 2.8 5H9.2C9.7 6 11 4 12 4zM4.3 11h4.8c0 .7 0 1.3.1 2H4.3a8 8 0 0 1 0-2zm.5 4h4.6c.4 1.9 1 3.5 1.7 4.7A8 8 0 0 1 4.8 15zm7.2 5c-1 0-2.3-2-2.8-5h5.6c-.5 3-1.8 5-2.8 5zm1-7h-2.2a17 17 0 0 1 0-2h2.2a17 17 0 0 1 0 2zm-.4 6.7c.7-1.2 1.3-2.8 1.7-4.7h4.6a8 8 0 0 1-6.3 4.7zM14.9 13c.1-.7.1-1.3.1-2h4.7a8 8 0 0 1 0 2z"/></svg></li>
      <li>rosalind.mercer@tolven-example.com
        <svg viewBox="0 0 24 24"><path d="M2 5h20v14H2zm2 2v.5l8 5 8-5V7zm0 2.8V17h16V9.8l-8 5z"/></svg></li>
    </ul>
    <ul class="taglines">
      <li>Smart Corporate Journeys</li>
      <li>Clearer Insight for Every Trip Budget</li>
    </ul>
  </section>

  <section class="card card-back">
    <div class="brand-back">
      <span class="brand-back-dot"></span>
      <span class="brand-back-name">tolvEn</span>
    </div>
  </section>
</body>
</html>
```